I have a logo and need to design the business card and stationery.
Updates

The uploaded logo image named as GREYMARSH CONSTRUCTION which is to be replaced to GREYMARSH CONTRACTS. Kindly add below details and submit the designs- Company name- Greymarsh Engineering Contracts LLP Name & Post- Kelvan Joshi (Designated Partner) Address- Block No.317, Wing C, Tulvo Trade Court, Manek Pural Road, Ruparel Industrial Estate, Goregaon(E), Mumbai - 400 063 Contact- +91 97415 60382 Email- kelvanjoshi@mailbrook.example Website- www.greymarshcontracts.example Contact for Letterhead- +91-22-28754193

Hi Tovin Rahul, We are liking your Design #28860835. We have suggested some changes which are mentioned in feedback. Kindly revert with it asap to finalize this design.

Colors

Designer to choose colors to be used in the design.

```html
<!DOCTYPE html>
<html lang="en">
<head>
<meta charset="utf-8">
<title>Greymarsh Contracts Letterhead</title>
<link rel="stylesheet" href="https://fonts.googleapis.com/css2?family=Mulish:wght@700;800&family=Arimo:wght@400&display=swap">
<style>
  :root {
    --backdrop: #d9d9d9;
    --paper: #fbfbfc;
    --ink-dark: #2f2f31;
    --ink-grey: #6d6d6d;
    --text: #575757;
    --rule: #8a8a8a;
    --signature: #b9b9bd;
  }
  * { margin: 0; padding: 0; box-sizing: border-box; }
  html, body {
    width: 1200px; height: 1079px; overflow: hidden;
    background: var(--backdrop);
  }
  .letterhead {
    position: absolute; left: 219px; top: 0;
    width: 762px; height: 1079px;
    background: var(--paper);
    overflow: hidden;
  }
  .header-band {
    position: absolute; left: 0; top: 0; width: 762px; height: 36px;
    background: var(--ink-dark);
  }
  .header-stripe {
    position: absolute; left: 0; top: 40px; width: 762px; height: 6px;
    background: var(--ink-grey);
  }
  .brand {
    position: absolute; left: 68px; top: 78px; width: 190px;
    display: flex; flex-direction: column; align-items: center; gap: 10px;
  }
  .brand-square { width: 46px; height: 46px; background: var(--ink-dark); }
  .brand-name {
    font-family: "Mulish", sans-serif; font-weight: 800;
    font-size: 20px; line-height: 22px; letter-spacing: 0.6px;
    color: var(--ink-dark); text-align: center;
  }
  .salutation {
    position: absolute; left: 69px; top: 331px;
    font-family: "Mulish", sans-serif; font-weight: 700;
    font-size: 18px; color: var(--text);
  }
  .body-copy {
    position: absolute; left: 68px; top: 380px; width: 626px;
    font-family: "Arimo", Arial, sans-serif; font-size: 13.1px; line-height: 15.6px;
    color: var(--text);
  }
  .body-copy p + p { margin-top: 13.5px; }
  .closing {
    position: absolute; left: 69px; top: 704px;
    font-family: "Mulish", sans-serif; font-weight: 700; font-size: 9.8px;
    color: var(--text);
  }
  .signature {
    position: absolute; left: 68px; top: 750px; width: 126px; height: 38px;
    background: linear-gradient(90deg, var(--signature), #d8d8dc);
    border-radius: 4px;
  }
  .footer-contacts {
    position: absolute; left: 0; width: 762px; top: 1001px;
    display: flex; justify-content: center; align-items: center; gap: 9px;
    font-family: "Arimo", Arial, sans-serif; font-size: 11px; color: var(--text);
  }
  .footer-contacts .item { display: flex; align-items: center; gap: 5px; }
  .footer-contacts svg { width: 10px; height: 10px; fill: var(--ink-dark); }
  .footer-rule {
    position: absolute; left: 91px; top: 1022px; width: 581px; height: 1.5px;
    background: var(--rule);
  }
  .footer-address {
    position: absolute; left: 0; width: 762px; top: 1029px; text-align: center;
    font-family: "Arimo", Arial, sans-serif; font-size: 10.6px; color: var(--ink-grey);
    white-space: nowrap;
  }
</style>
</head>
<body>
  <div class="letterhead">
    <div class="header-band"></div>
    <div class="header-stripe"></div>

    <div class="brand">
      <div class="brand-square"></div>
      <div class="brand-name">GREYMARSH<br>CONTRACTS</div>
    </div>

    <div class="salutation">Dear Mr. Smith,</div>

    <div class="body-copy">
      <p>Lorem ipsum dolor sit amet, consectetuer adipiscing elit, sed diam nonmmy nibh euismod tincidunt ut laor eet dolore magna aliquam erat volutpat. Ut wisi enim ad minim veniam, quis nostrud exerci tationmcorper suscipit lobortis nisl ut aliquip ex ea commodo consequat. Duis autem vel eum iriure dolor in hendrerit in vulputate velit esse molestie consequat, vel illum dolore eu feugiat</p>
      <p>Rorem ipsum dolor sit amet, consectetuer adipiscing elit, sed diam nonmmy nibh euismod tincidunt ut laor eet dolore magna aliquam erat volutpat. Ut wisi enim ad minim veniam, quis nostrud exerci tationmcorper suscipit lobortis nisl ut aliquip ex ea commodo consequat. Duis autem vel eum iriure dolor in hendrerit in vulputate velit esse molest</p>
      <p>Dorem ipsum dolor sit amet, consectetuer adipiscing elit, sed diam nonmmy nibh euismod tincidunt ut laor eet dolore magna aliquam erat volutpat. Ut wisi enim ad minim veniam, quis nostrud exerci tationmcorper suscipit lobortis nisl ut aliquip ex ea commodo consequat. Duis autem vel eum iriure dolor in hendrerit in suscipit lobortis nisl ut aliquip ex ea commodo consequat. Duis autem vel eum iriure dolor in hendrerit in vulputate velit esse molestie consequat, vel illum</p>
      <p>Sorem ipsum dolor sit amet, consectetuer adipiscing elit, sed diam nonmmy nibh euismod tincidunt ut laor eet dolore magna aliquam erat volutpat. Ut wisi enim ad minim veniam, quis nostrud exerci tationmcorper suscipit lobortis nisl ut aliquip ex ea commodo consequat. Duis autem vel eum iriure dolor in</p>
    </div>

    <div class="closing">Sincerely,</div>
    <div class="signature" role="img" aria-label="Handwritten signature"></div>

    <div class="footer-contacts">
      <span class="item">
        <svg viewBox="0 0 24 24"><path d="M6.6 10.8a15.1 15.1 0 0 0 6.6 6.6l2.2-2.2a1 1 0 0 1 1-.25 11.4 11.4 0 0 0 3.6.57 1 1 0 0 1 1 1V20a1 1 0 0 1-1 1A17 17 0 0 1 3 4a1 1 0 0 1 1-1h3.5a1 1 0 0 1 1 1c0 1.25.2 2.45.57 3.6a1 1 0 0 1-.25 1z"/></svg>
        +91-22-28754193
      </span>
      <span class="item">
        <svg viewBox="0 0 24 24"><path d="M2 5h20v14H2z M2 5l10 8 10-8" stroke="#fbfbfc" stroke-width="1.5"/></svg>
        kelvanjoshi@mailbrook.example
      </span>
      <span class="item">
        <svg viewBox="0 0 24 24"><circle cx="12" cy="12" r="10"/><path d="M2 12h20M12 2c3 3 3 17 0 20M12 2c-3 3-3 17 0 20" stroke="#fbfbfc" stroke-width="1.5" fill="none"/></svg>
        www.greymarshcontracts.example
      </span>
    </div>
    <div class="footer-rule"></div>
    <div class="footer-address">Block No.317, Wing C, Tulvo Trade Court, Manek Pural Road, Ruparel Industrial Estate, Goregaon(E), Mumbai - 400 063</div>
  </div>
</body>
</html>
```